Beauty Therapy Web Design

I need a web page design for a small beauty therapy clinic, the owner is currently the only beauty therapist working there.
We require the following pages:
Home
About
Treatments
Nails
Courses
Contact
I will attach the clinics business card, treatment menu and signage so that you get a feeling for the branding colours etc.
This is the first website for the beauty therapist, she would like to attract new clients and also tourists that come in on the cruise ships. The thing that sets her apart from other clinics is that she welcomes texting for appointments.
I have selected refundable because I have never done this before so I don't know what to expect, I have the full intention of going through with it as long as I get a good design.
Feel free to ask for further information
Reason: Project extended as I am away for work and am unable to meet with the owner.
Target Market(s)
Females 18 to 50
Industry/Entity Type
Business
Look and feel

```html
<!DOCTYPE html>
<html lang="en">
<head>
<meta charset="utf-8">
<title>Lumina Beauty Therapy</title>
<link href="https://fonts.googleapis.com/css2?family=Arimo:wght@400;700&display=swap" rel="stylesheet">
<style>
:root{
  --purple:#5e2289;
  --purple-dark:#4a1b6e;
  --ink:#3f1570;
  --gold:#f7b500;
  --btn-top:#9a7cf2;
  --btn-bottom:#5a2fd0;
  --rule:#d9d0ec;
  --footer-top:#f1eff7;
}
*{box-sizing:border-box;margin:0;padding:0}
html,body{width:921px;height:1200px;overflow:hidden;background:#fff}
body{font-family:"Arimo",Helvetica,Arial,sans-serif;position:relative}
.page{position:absolute;left:36px;top:0;width:849px;height:1200px}

.site-header{position:absolute;top:39px;left:0;width:849px;height:145px;background:var(--purple)}
.brand{position:absolute;left:56px;top:14px;color:var(--gold);font-weight:700;line-height:1}
.brand-name{display:block;font-size:66px;letter-spacing:-1px}
.brand-sub{display:block;font-size:31px;margin-top:6px;letter-spacing:.5px}
.contact-block{position:absolute;right:54px;top:34px;text-align:right;color:#fff;font-weight:700}
.contact-block p{font-size:13px;line-height:22px}
.contact-block .num{font-size:16px;margin-left:4px}
.address{position:absolute;right:54px;top:107px;color:#fff;font-weight:700;font-size:13px}

.main-nav{position:absolute;top:193px;left:0;width:849px;height:22px;background:var(--purple-dark)}
.main-nav ul{list-style:none;display:flex;margin-left:118px;height:22px;border-left:1px solid #fff}
.main-nav li{height:22px;border-right:1px solid #fff;color:#fff;font-size:11px;font-weight:700;display:flex;align-items:center;justify-content:center}

.hero{position:absolute;top:225px;left:0;width:849px;height:454px}
.hero-photo{position:absolute;left:0;top:0;width:488px;height:454px;background:linear-gradient(135deg,#f1dfe6 0%,#e8c9d6 35%,#c6b0e4 60%,#8f6bd0 85%,#6f4cb8 100%)}
.hero-panel{position:absolute;left:488px;top:0;width:361px;height:454px;background:linear-gradient(160deg,#3a2824 0%,#34213c 45%,#3c1f62 100%);color:#fff;padding:42px 30px 0 58px}
.hero-panel h2{font-size:27px;font-weight:700;letter-spacing:.3px}
.lead{font-size:12.5px;font-weight:700;line-height:22.7px;margin-top:20px}
.hero-panel .body{font-size:12.5px;line-height:22.7px;margin-top:20px}
.btn{display:flex;align-items:center;justify-content:center;width:181px;height:36px;border-radius:18px;background:linear-gradient(180deg,var(--btn-top),var(--btn-bottom));color:#fff;font-size:18px;font-weight:700;text-shadow:0 1px 2px rgba(40,10,90,.7);box-shadow:0 2px 2px rgba(50,20,110,.5)}
.hero-panel .btn{margin-top:26px}
.dots{display:flex;gap:7.5px;margin-top:26px;margin-left:36px}
.dots span{width:17px;height:17px;border-radius:50%;background:radial-gradient(circle at 40% 35%,#a58af5,#5a33d0)}
.dots span.active{background:radial-gradient(circle at 40% 35%,#fff,#c4b4f2)}

.features{position:absolute;top:679px;left:0;width:849px;height:365px}
.features::before{content:"";position:absolute;left:488px;top:0;width:1px;height:365px;background:var(--rule)}
.feature{position:absolute;top:30px;color:var(--ink)}
.feature-left{left:50px;width:410px}
.feature-right{left:543px;width:290px}
.feature h3{font-size:26px;font-weight:700;letter-spacing:.2px}
.feature .lead{margin-top:22px}
.feature .body{font-size:12.5px;line-height:22.7px;margin-top:20px}
.feature .btn{margin-top:26px}

.site-footer{position:absolute;top:1044px;left:0;width:849px;height:146px;background:linear-gradient(180deg,var(--footer-top),#fff);text-align:center;color:var(--ink);font-size:12px;line-height:22px;padding-top:29px}
</style>
</head>
<body>
<div class="page">
  <header class="site-header">
    <div class="brand"><span class="brand-name">Lumina</span><span class="brand-sub">BEAUTY THERAPY</span></div>
    <div class="contact-block">
      <p>Phone Tessa <span class="num">07 555 0142</span></p>
      <p>Cellphone <span class="num">027 555 0199</span></p>
    </div>
    <p class="address">Cnr Kowhai St. &amp; Harbour Rd, Seaview Bay</p>
  </header>

  <nav class="main-nav">
    <ul>
      <li style="width:85px">HOME</li>
      <li style="width:92px">ABOUT</li>
      <li style="width:129px">TREATMENTS</li>
      <li style="width:85px">NAILS</li>
      <li style="width:115px">COURSES</li>
      <li style="width:106px">CONTACT</li>
    </ul>
  </nav>

  <section class="hero">
    <div class="hero-photo" role="img" aria-label="Close-up photo of manicured hands with floral nail art and purple flowers"></div>
    <div class="hero-panel">
      <h2>NULLAM ALIQUAM</h2>
      <p class="lead">Homero nostrum definitionem<br>mea et, his no malis</p>
      <p class="body">Homero nostrum definitionem mea et, his no malis ullamcorper, cu tollit nostrum pri. Qui id nusquam docendi inimicus, tota iusto mea eu. Mea cu paulo mollis, ad nam vide inciderint necessitatibus. Pri cu integre</p>
      <a class="btn">Read more</a>
      <div class="dots"><span></span><span class="active"></span><span></span><span></span><span></span></div>
    </div>
  </section>

  <section class="features">
    <article class="feature feature-left">
      <h3>NULLAM ALIQUAM SAPERET</h3>
      <p class="lead">Homero nostrum definitionem mea et, his no malis ullamcorper, cu tollit nostrum pri. Qui id nusquam docendi</p>
      <p class="body">Homero nostrum definitionem mea et, his no malis ullamcorper, cu tollit nostrum pri. Qui id nusquam docendi inimicus, tota iusto mea eu. Mea cu paulo mollis, ad nam vide inciderint necessitatibus. Pri cu integre assueverit, veri tritani facilisi pri ad. Per ne apeirian expetendis, ei fastidii patrioque gubergren sea. Vim odio vivendum</p>
      <a class="btn">Read more</a>
    </article>
    <article class="feature feature-right">
      <h3>NULLAM ALIQUAM</h3>
      <p class="lead">Homero nostrum definitionem<br>mea et, his no malis</p>
      <p class="body">Homero nostrum definitionem mea et, his no malis ullamcorper, cu tollit nostrum pri. Qui id nusquam docendi inimicus, tota iusto mea eu. Mea cu paulo mollis, ad nam vide inciderint necessitatibus. Pri cu integre</p>
      <a class="btn">Read more</a>
    </article>
  </section>

  <footer class="site-footer">
    <p>Copyright 2012 Lumina Beauty Therapy</p>
    <p>Phone Tessa 07 555 0142&nbsp;&nbsp;&nbsp;&nbsp;Cellphone 027 555 0199</p>
    <p>Cnr Kowhai St. &amp; Harbour Rd, Seaview Bay</p>
  </footer>
</div>
</body>
</html>
```